indépendant en tant que Massothérapeute et Préparateur Mental, j'ai besoin de ...

Massothérapeute et préparateur mental indépendant, je recherche une carte de visite sobre et dynamique, sans images liées au massage ou à la préparation mentale mais intégrant mon logo. Les couleurs que j'aime bien sont : Blanc, gris, anthracite, noir et jaune

Contact Information for Business Card

carte de préférence Horizontale
neutre qui puisse toucher le deux domaines Massothérapie et préparation mentale

Requirements
Must have
• mon projet doit intégrer au recto:
LOGO
Loïc Bardèze
078 513 26 48
info@loicbardeze.ch
et éventuellement www.loicbardeze.ch

et au verso les deux adresses:

Chemin des Ormilles 7B
1400 Yverdon-les-Bains

Route de la Gravière 9
1700 Fribourg

Should not have
• mon projet ne doit pas contenir d'image en liens avec le massage ni la préparation mentale.

```html
<!DOCTYPE html>
<html lang="fr">
<head>
<meta charset="utf-8">
<title>Loïc Bardèze – Carte de visite</title>
<link href="https://fonts.googleapis.com/css2?family=Josefin+Sans:wght@300;400;600;700&display=swap" rel="stylesheet">
<style>
  :root {
    --backdrop: #a3cdb8;
    --anthracite: #3a3a3a;
    --paper: #f4f4f3;
    --ink-light: #ffffff;
    --ink-soft: #e4e4e4;
    --ink-muted: #9a9a9a;
    --ink-dark: #3a3a3a;
  }
  * { margin: 0; padding: 0; box-sizing: border-box; }
  html, body {
    width: 1200px; height: 900px; overflow: hidden;
    background: var(--backdrop);
    font-family: "Josefin Sans", sans-serif;
  }
  .card {
    position: absolute;
    left: 401px;
    width: 413px;
    height: 238px;
    box-shadow: 0 3px 10px rgba(0,0,0,0.18);
  }
  .card--front { top: 196px; background: var(--anthracite); color: var(--ink-light); }
  .card--back  { top: 477px; background: var(--paper); color: var(--ink-dark); }

  .brand { position: absolute; display: flex; align-items: center; gap: 8px; }
  .brand__dot { width: 22px; height: 22px; border-radius: 50%; background: currentColor; flex: none; }
  .brand__text { display: flex; flex-direction: column; }
  .brand__name { font-weight: 700; font-size: 20px; letter-spacing: 0.5px; line-height: 1; }
  .brand__role { font-weight: 600; font-size: 6.5px; letter-spacing: 0.4px; text-transform: uppercase; margin-top: 3px; }

  .card--front .brand { left: 36px; top: 50px; }
  .card--back .brand { left: 212px; top: 183px; gap: 6px; }
  .card--back .brand__dot { width: 16px; height: 16px; }
  .card--back .brand__name { font-size: 14px; }
  .card--back .brand__role { font-size: 5px; margin-top: 2px; }

  .holder {
    position: absolute; left: 61px; top: 104px;
    font-weight: 600; font-size: 16.5px; letter-spacing: 1px;
    text-transform: uppercase;
  }
  .contact-rule { position: absolute; left: 51px; top: 127px; width: 1px; height: 65px; background: var(--ink-muted); }
  .contact-list { position: absolute; left: 60px; top: 131px; list-style: none; }
  .contact-list li {
    display: flex; align-items: center; gap: 8px;
    height: 20px; font-weight: 300; font-size: 12px; color: var(--ink-soft);
  }
  .contact-list svg { width: 12px; height: 12px; fill: var(--ink-muted); flex: none; }

  .address-list { position: absolute; left: 64px; top: 81px; list-style: none; }
  .address-list li { display: flex; align-items: center; gap: 8px; margin-bottom: 15px; }
  .address-list svg { width: 16px; height: 20px; fill: var(--ink-dark); flex: none; }
  .address-list p { font-weight: 400; font-size: 12px; line-height: 14.5px; }
</style>
</head>
<body>
  <section class="card card--front">
    <div class="brand">
      <span class="brand__dot"></span>
      <div class="brand__text">
        <span class="brand__name">Loïc Bardèze</span>
        <span class="brand__role">Massothérapeute / Préparateur Mental</span>
      </div>
    </div>
    <h1 class="holder">Loïc Bardèze</h1>
    <span class="contact-rule"></span>
    <ul class="contact-list">
      <li>
        <svg viewBox="0 0 24 24" aria-hidden="true"><path d="M6.6 10.8a15.1 15.1 0 0 0 6.6 6.6l2.2-2.2a1 1 0 0 1 1-.25 11.4 11.4 0 0 0 3.6.57 1 1 0 0 1 1 1V20a1 1 0 0 1-1 1A17 17 0 0 1 3 4a1 1 0 0 1 1-1h3.5a1 1 0 0 1 1 1c0 1.25.2 2.45.57 3.57a1 1 0 0 1-.25 1z"/></svg>
        078 513 26 48
      </li>
      <li>
        <svg viewBox="0 0 24 24" aria-hidden="true"><path d="M2 5h20v14H2z M3 6l9 7 9-7" /></svg>
        info@loicbardeze.ch
      </li>
      <li>
        <svg viewBox="0 0 24 24" aria-hidden="true"><circle cx="12" cy="12" r="10"/></svg>
        www.loicbardeze.ch
      </li>
    </ul>
  </section>

  <section class="card card--back">
    <ul class="address-list">
      <li>
        <svg viewBox="0 0 16 20" aria-hidden="true"><path d="M8 0a7 7 0 0 0-7 7c0 5 7 13 7 13s7-8 7-13a7 7 0 0 0-7-7zm0 9.5A2.5 2.5 0 1 1 8 4.5a2.5 2.5 0 0 1 0 5z"/></svg>
        <p>Chemin des Ormilles 7B<br>1400 Yverdon-les-Bains</p>
      </li>
      <li>
        <svg viewBox="0 0 16 20" aria-hidden="true"><path d="M8 0a7 7 0 0 0-7 7c0 5 7 13 7 13s7-8 7-13a7 7 0 0 0-7-7zm0 9.5A2.5 2.5 0 1 1 8 4.5a2.5 2.5 0 0 1 0 5z"/></svg>
        <p>Route de la Gravière 9<br>1700 Freiburg</p>
      </li>
    </ul>
    <div class="brand">
      <span class="brand__dot"></span>
      <div class="brand__text">
        <span class="brand__name">Loïc Bardèze</span>
        <span class="brand__role">Massothérapeute / Préparateur Mental</span>
      </div>
    </div>
  </section>
</body>
</html>
```